Single-sided business card for restaurant velmora with new logo made on this site

Business card options with new logo including restaurant name, address, phone number and website. This business card is single-sided only and will be presented at the hostess desk for clients to take. I would like to see options based on a cream card background, a white card background, a yellow card background and a burgundy colored background. It needs to be elegant and traditional.

Target Market(s)

local and international crowd

Industry/Entity Type

restaurant

Contact Information for Business Card

address, website and phone number

Font styles to use
Serif

Colors
EE7325
F08F49
F5BC92
FAE3D3
FDF4ED

Requirements
Must have
• new logo, address, phone number, website
Should not have
• more than three colors

```html
<!DOCTYPE html>
<html lang="es">
<head>
<meta charset="utf-8">
<title>Restaurant Velmora – tarjetas de presentación</title>
<link href="https://fonts.googleapis.com/css2?family=Source+Sans+3:wght@400;600&display=swap" rel="stylesheet">
<style>
  :root {
    --stage: #8f8f8f;
    --wine-dark: #3b1419;
    --cream: #feecd1;
    --cream-light: #fdf6e6;
    --burgundy: #7a1114;
    --marigold: #f7b33d;
    --white: #ffffff;
    --ink: #3b1419;
  }
  * { margin: 0; padding: 0; box-sizing: border-box; }
  html, body { width: 683px; height: 1200px; overflow: hidden; background: var(--stage); }
  body { position: relative; font-family: "Source Sans 3", "Segoe UI", sans-serif; }

  .card {
    position: absolute; left: 92px; width: 495px; height: 283px; overflow: hidden;
    --card-bg: var(--cream); --accent: var(--cream-light); --text: var(--ink);
    --title: var(--white); --mark: var(--wine-dark); --icon: var(--marigold);
    background: var(--card-bg); color: var(--text);
  }
  .card--cream { top: 91px; }
  .card--burgundy { top: 451px; --card-bg: var(--burgundy); --accent: var(--marigold); --text: var(--white); --title: var(--marigold); --mark: var(--white); }
  .card--white { top: 811px; --card-bg: var(--white); --accent: var(--marigold); }

  .card__shapes { position: absolute; inset: 0; width: 495px; height: 283px; }
  .card__shapes .header-tab { fill: var(--wine-dark); }
  .card__shapes .accent { fill: var(--accent); }

  .card__title {
    position: absolute; left: 0; width: 495px; top: 31px; text-align: center;
    padding-left: 2px; font-size: 24px; font-weight: 400; color: var(--title); letter-spacing: 0.1px;
  }

  .contact { position: absolute; font-size: 12.7px; line-height: 19.8px; }
  .contact--address { left: 82px; top: 113px; }
  .contact--reach { left: 281px; top: 110px; line-height: 22.6px; }

  .icon { position: absolute; width: 14px; height: 14px; fill: none; stroke: var(--icon); stroke-width: 1.3; stroke-linecap: round; stroke-linejoin: round; }
  .icon--pin { left: 142px; top: 208px; }
  .icon--phone { left: 249px; top: 206px; }
  .icon--pointer { left: 251px; top: 228px; }

  .brand { position: absolute; left: 0; width: 495px; top: 183px; display: flex; flex-direction: column; align-items: center; }
  .brand__square { width: 42px; height: 41px; background: var(--mark); }
  .brand__name { margin-top: 4px; font-size: 14px; font-weight: 600; letter-spacing: 3px; padding-left: 3px; color: var(--mark); }
</style>
</head>
<body>

<section class="card card--cream" aria-label="Tarjeta crema">
  <svg class="card__shapes" viewBox="0 0 495 283" aria-hidden="true">
    <path class="header-tab" d="M61,0 L430,0 C420,38 410,73 372,73 L118,73 C84,73 72,42 61,0Z"/>
    <path class="accent" d="M0,90 Q10,90 10,100 L10,188 Q10,198 0,198Z"/>
    <path class="accent" d="M495,90 Q485,90 485,100 L485,188 Q485,198 495,198Z"/>
    <path class="accent" d="M192,283 L192,272 Q192,262 204,262 L290,262 Q302,262 302,272 L302,283Z"/>
  </svg>
  <h1 class="card__title">Restaurant Velmora</h1>
  <p class="contact contact--address">Jacaranda 415<br>Bahías de Huatulco,<br>Oaxaca CP 70980</p>
  <p class="contact contact--reach">Reservaciones 958-555-0142<br>www.velmora.com.mx</p>
  <div class="brand"><span class="brand__square"></span><span class="brand__name">VELMORA</span></div>
</section>

<section class="card card--burgundy" aria-label="Tarjeta burdeos">
  <svg class="card__shapes" viewBox="0 0 495 283" aria-hidden="true">
    <path class="header-tab" d="M61,0 L430,0 C420,38 410,73 372,73 L118,73 C84,73 72,42 61,0Z" stroke="#ffffff" stroke-width="1.6"/>
    <path class="accent" d="M0,90 Q10,90 10,100 L10,188 Q10,198 0,198Z"/>
    <path class="accent" d="M495,90 Q485,90 485,100 L485,188 Q485,198 495,198Z"/>
    <path class="accent" d="M192,283 L192,272 Q192,262 204,262 L290,262 Q302,262 302,272 L302,283Z"/>
  </svg>
  <h1 class="card__title">Restaurant Velmora</h1>
  <p class="contact contact--address">Jacaranda 415<br>Bahías de Huatulco,<br>Oaxaca CP 70980</p>
  <p class="contact contact--reach">Reservaciones 958-555-0142<br>www.velmora.com.mx</p>
  <div class="brand"><span class="brand__square"></span><span class="brand__name">VELMORA</span></div>
</section>

<section class="card card--white" aria-label="Tarjeta blanca">
  <svg class="card__shapes" viewBox="0 0 495 283" aria-hidden="true">
    <path class="header-tab" d="M61,0 L430,0 C420,38 410,73 372,73 L118,73 C84,73 72,42 61,0Z"/>
    <path class="accent" d="M0,90 Q10,90 10,100 L10,188 Q10,198 0,198Z"/>
    <path class="accent" d="M495,90 Q485,90 485,100 L485,188 Q485,198 495,198Z"/>
    <path class="accent" d="M192,283 L192,272 Q192,262 204,262 L290,262 Q302,262 302,272 L302,283Z"/>
  </svg>
  <h1 class="card__title">Restaurant Velmora</h1>
  <p class="contact contact--address">Jacaranda 415<br>Bahías de Huatulco,<br>Oaxaca CP 70980</p>
  <p class="contact contact--reach">Reservaciones 958-555-0142<br>www.velmora.com.mx</p>
  <div class="brand"><span class="brand__square"></span><span class="brand__name">VELMORA</span></div>
</section>

<svg width="0" height="0" style="position:absolute" aria-hidden="true">
  <defs>
    <symbol id="icon-pin" viewBox="0 0 14 14"><path d="M7,13 C4,9.5 2.5,7.2 2.5,5.3 A4.5,4.5 0 0 1 11.5,5.3 C11.5,7.2 10,9.5 7,13Z"/><circle cx="7" cy="5.3" r="1.6"/></symbol>
    <symbol id="icon-phone" viewBox="0 0 14 14"><path d="M2.5,2 L4.8,1.8 L6,4.8 L4.6,5.9 C5.4,7.7 6.3,8.6 8.1,9.4 L9.2,8 L12.2,9.2 L12,11.5 C7,12 2,7 2.5,2Z"/><path d="M8.3,1.6 A4.2,4.2 0 0 1 12.4,5.7"/><path d="M8.1,3.6 A2.2,2.2 0 0 1 10.4,5.9"/></symbol>
    <symbol id="icon-pointer" viewBox="0 0 14 14"><path d="M2.5,1.5 L11,7.5 L7.3,8.2 L9.5,12.2 L8,13 L5.8,9 L3,11.4Z"/></symbol>
  </defs>
</svg>

<svg class="icon" style="left:234px;top:206px" viewBox="0 0 14 14" aria-hidden="true"><use href="#icon-pin"/></svg>
<svg class="icon" style="left:341px;top:204px" viewBox="0 0 14 14" aria-hidden="true"><use href="#icon-phone"/></svg>
<svg class="icon" style="left:342px;top:228px" viewBox="0 0 14 14" aria-hidden="true"><use href="#icon-pointer"/></svg>

<svg class="icon" style="left:234px;top:566px" viewBox="0 0 14 14" aria-hidden="true"><use href="#icon-pin"/></svg>
<svg class="icon" style="left:341px;top:564px" viewBox="0 0 14 14" aria-hidden="true"><use href="#icon-phone"/></svg>
<svg class="icon" style="left:342px;top:588px" viewBox="0 0 14 14" aria-hidden="true"><use href="#icon-pointer"/></svg>

<svg class="icon" style="left:234px;top:926px" viewBox="0 0 14 14" aria-hidden="true"><use href="#icon-pin"/></svg>
<svg class="icon" style="left:341px;top:924px" viewBox="0 0 14 14" aria-hidden="true"><use href="#icon-phone"/></svg>
<svg class="icon" style="left:342px;top:948px" viewBox="0 0 14 14" aria-hidden="true"><use href="#icon-pointer"/></svg>

</body>
</html>
```